Key Scientific Research Plastics Presentation - 5 Slides

We need the attached slides reworked with the following changes:

Information needs to be very visually stunning and easily understood
Text/font treatments should attract attention
All graphs and infographics can be recreated to match style
Attached color palette is not necessary, but can be used

Please reach out with any questions.

```html
<!DOCTYPE html>
<html lang="en">
<head>
<meta charset="utf-8">
<title>Foam Science Council – Scientific Research Plastics</title>
<link rel="stylesheet" href="https://fonts.googleapis.com/css2?family=Poppins:ital,wght@0,400;0,500;0,600;0,700;1,400&display=swap">
<style>
:root{
  --brown:#6b2a14;
  --blue:#5a88a6;
  --olive:#a3a63b;
  --orange:#f6a21f;
  --orange-dark:#c77a0c;
  --cream:#f6f1e2;
  --ink:#2b2b2b;
  --page:#efefef;
  --row:#f1f1f1;
}
*{box-sizing:border-box;margin:0;padding:0}
html,body{width:1105px;height:1200px;overflow:hidden;background:var(--page);font-family:"Poppins",sans-serif;color:var(--ink)}
.board{position:absolute;left:0;top:0;width:1848px;height:2008px;transform:scale(0.598);transform-origin:0 0}
.slide{position:absolute;width:804px;height:452px;background:#fff;overflow:hidden}
.col-l{left:81px}.col-r{left:966px}
.row-1{top:46px}.row-2{top:521px}.row-3{top:998px}.row-4{top:1476px}
.abs{position:absolute}
.bar{position:absolute;left:50%;top:17px;width:50px;height:5px;margin-left:-25px;background:var(--blue)}
.bar.white{background:#fff}
.title{position:absolute;left:0;right:0;text-align:center;color:var(--brown);font-weight:600;font-size:31px;line-height:1.15}
.title .light{font-weight:400}
.subtitle{position:absolute;left:0;right:0;text-align:center;color:var(--blue);font-size:20px;line-height:1.2}
.lead{position:absolute;left:30px;right:30px;text-align:center;font-size:11.5px;line-height:20px}
.panel{position:absolute;background:var(--olive);border-radius:8px;color:#fff;font-style:italic}
.pagenum{position:absolute;right:10px;bottom:8px;width:22px;height:22px;border-radius:50%;background:#111;color:#fff;font-size:10px;font-weight:600;display:flex;align-items:center;justify-content:center}
.pagenum.plain{background:none}

/* slide 1 */
.cover{background:linear-gradient(120deg,#5f8790 0%,#7e9a72 40%,#a8a33a 70%,#c99a1a 100%)}
.cover .ring{position:absolute;left:406px;top:42px;width:370px;height:370px;border-radius:50%;background:var(--orange)}
.cover .photo{position:absolute;left:424px;top:42px;width:362px;height:362px;border-radius:50%;background:radial-gradient(circle at 45% 40%,#6fa9b6,#2f5f6e 70%,#1f3e4a)}
.cover .brand{position:absolute;left:30px;top:86px;display:flex;align-items:center;gap:14px}
.cover .brand-dot{width:124px;height:124px;border-radius:50%;background:#fff;flex:none}
.cover .brand-name{color:#fff;font-size:22px;font-weight:400;line-height:1.15}
.cover h1{position:absolute;left:29px;top:238px;color:#fff;font-size:44px;font-weight:700;line-height:1}
.cover .tag{position:absolute;left:29px;top:340px;color:#fff;font-size:26px;font-weight:600}

/* slide 2 */
.risk .panel{left:10px;top:112px;width:290px;height:310px;padding:16px 16px;font-size:11.5px;line-height:25px}
.node{position:absolute;border-radius:50%;display:flex;align-items:center;justify-content:center;color:#fff;text-align:center}
.node.core{left:418px;top:162px;width:90px;height:90px;background:var(--blue);font-size:12px;font-weight:600;line-height:1.2}
.node.sm{width:44px;height:44px}
.node.sm::after{content:"";width:18px;height:18px;border:2px solid #fff;border-radius:50%}
.lbl{position:absolute;font-size:11px;font-weight:600;color:var(--brown);line-height:1.2}
.note{position:absolute;left:652px;top:174px;width:140px;font-size:9.5px;font-style:italic;color:var(--blue);line-height:16.5px}
.rating-h{position:absolute;left:320px;right:0;text-align:center;top:286px;font-size:20px;font-weight:600;color:var(--brown)}
.rating{position:absolute;top:326px;width:230px;font-size:9px;line-height:14px}
.rating h4{color:var(--brown);font-size:11px;font-weight:600;text-decoration:underline;margin-bottom:3px}

/* slide 3 */
.treaty .panel{left:12px;top:120px;width:290px;height:261px;padding:14px 17px;font-size:17px;line-height:25.5px}
.checks{position:absolute;left:334px;top:125px;width:460px;list-style:none}
.checks li{display:flex;gap:12px;font-size:13px;line-height:21px;margin-bottom:13px}
.checks svg{flex:none;width:16px;height:16px;margin-top:2px}
.treaty .foot{position:absolute;left:0;right:0;top:404px;text-align:center;color:var(--blue);font-size:21px;font-weight:600}

/* slide 4 */
.eps-table{position:absolute;left:14px;top:165px;width:379px;border-collapse:collapse;font-size:12.5px}
.eps-table th{background:var(--blue);color:#fff;font-weight:500;text-align:left;padding:6px 12px;line-height:1.2;font-size:12.5px}
.eps-table td{background:var(--row);padding:0 12px;height:49px;border-bottom:1px solid #cfd7de;line-height:1.25}
.eps-table td+td{text-align:center}
.chart{position:absolute;left:0;top:0;width:804px;height:452px}

/* slide 5 */
.misuse .claim{position:absolute;left:43px;top:127px;width:718px;height:108px;background:var(--cream);border-radius:8px}
.claim .org{position:absolute;left:14px;top:12px;width:86px;display:flex;flex-direction:column;align-items:center;gap:6px}
.claim .org-mark{width:30px;height:30px;border:2px solid var(--ink)}
.claim .org-name{font-size:10px;font-weight:600;color:var(--ink);text-align:center;line-height:1.15}
.claim .txt{position:absolute;left:108px;top:16px;right:30px;font-size:12.5px;line-height:21px}
.claim b,.concl b{color:var(--brown);font-weight:600}
.claim .ref{position:absolute;left:108px;top:70px;font-size:11px;color:var(--brown)}
.paper{position:absolute;left:41px;top:260px;width:181px;height:172px;border:1px solid #bbb;border-radius:6px;background:#fff;padding:18px 12px}
.paper .jn{text-align:right;color:#c0392b;font-size:9px;font-weight:600;line-height:1}
.paper .pt{font-size:9.5px;font-weight:600;line-height:1.2;margin-top:18px}
.paper .ln{height:3px;background:#cfcfcf;margin-top:4px}
.concl{position:absolute;left:238px;top:294px;width:546px;font-size:12.5px;line-height:20.5px}
.concl .hl{color:#e08a10}

/* slide 6 */
.break{background:radial-gradient(ellipse at 40% 40%,#7ca632 0%,#5f8a2a 45%,#6b8428 75%,#8a8d2a 100%)}
.centered{position:absolute;left:0;right:0;text-align:center;color:#fff}
.break .h{top:168px;font-size:32px;font-weight:600}
.break .p{top:218px;left:50px;right:50px;font-size:17.5px;line-height:26px}

/* slide 7 */
.atmo .panel{left:12px;top:177px;width:290px;height:224px;padding:14px 16px;font-size:13px;line-height:22.4px}
.atmo .body{position:absolute;left:329px;top:170px;width:460px;font-size:11.5px;line-height:19px}
.atmo .body u{color:var(--brown);font-weight:600}
.atmo ul{list-style:none;margin:4px 0 8px}
.atmo li{position:relative;padding-left:20px;font-size:11px;line-height:17px;margin-bottom:2px}
.atmo li::before{content:"";position:absolute;left:2px;top:4px;width:8px;height:4px;border-left:2px solid var(--brown);border-bottom:2px solid var(--brown);transform:rotate(-45deg)}

/* slide 8 */
.thanks{background:linear-gradient(110deg,#5a1409 0%,#7a2a12 35%,#4a3a14 65%,#1f3a1c 100%)}
.thanks .h{top:138px;font-size:40px;font-weight:600}
.thanks .h span{font-weight:400}
.thanks .p{top:206px;left:60px;right:60px;font-size:14px;line-height:25px}
.social{position:absolute;left:318px;top:296px;display:flex;gap:28px}
.social span{width:37px;height:37px;border:2px solid #fff;border-radius:50%}
</style>
</head>
<body>
<div class="board">

  <!-- cover -->
  <section class="slide col-l row-1 cover">
    <div class="ring"></div>
    <div class="photo" role="img" aria-label="Photo of a laboratory scientist in safety glasses handling a sample"></div>
    <div class="brand"><span class="brand-dot"></span><span class="brand-name">Foam Science<br>Council</span></div>
    <h1>Foam Science<br>Council</h1>
    <p class="tag">Scientific Research Plastics</p>
  </section>

  <!-- risk vs exposure -->
  <section class="slide col-r row-1 risk">
    <div class="bar"></div>
    <h2 class="title" style="top:26px;font-size:31px">Understanding Risk Versus Exposure</h2>
    <p class="lead" style="top:64px">Any substance can be poisonous. Chemicals of concern must be evaluated within typical use parameters to evaluate its potential to present a hazard.</p>
    <div class="panel">National Risk Review Database (NRRD) cautions that “NRRD values cannot be validly used to accurately predict the incidence of human disease or the type of effects that chemical exposures have on humans. This is due to the numerous uncertainties involved in risk assessment, including those associated with extrapolations from animal data to humans and from high experimental doses to lower environmental exposures.”</div>
    <svg class="abs" style="left:0;top:0" width="804" height="300" aria-hidden="true">
      <g stroke="#6b2a14" stroke-width="1"><line x1="405" y1="155" x2="463" y2="207"/><line x1="390" y1="206" x2="463" y2="207"/><line x1="403" y1="255" x2="463" y2="207"/><line x1="532" y1="176" x2="463" y2="207"/><line x1="532" y1="236" x2="463" y2="207"/></g>
    </svg>
    <div class="node sm" style="left:383px;top:133px;background:#c8901e"></div>
    <div class="node sm" style="left:368px;top:184px;background:var(--orange)"></div>
    <div class="node sm" style="left:381px;top:233px;background:#6b2a14"></div>
    <div class="node sm" style="left:510px;top:154px;background:var(--olive)"></div>
    <div class="node sm" style="left:510px;top:214px;background:#5c5c5c"></div>
    <div class="node core">Risk of<br>Exposure</div>
    <span class="lbl" style="left:324px;top:150px">Duration</span>
    <span class="lbl" style="left:312px;top:199px">Toxicity</span>
    <span class="lbl" style="left:345px;top:249px">Dose</span>
    <span class="lbl" style="left:562px;top:169px">Frequency</span>
    <span class="lbl" style="left:562px;top:222px">Route of<br>Exposure</span>
    <p class="note">Risk Assessment Involves Reasonable Assumptions Under Different Exposure Scenarios To Determine Toxicity Levels</p>
    <h3 class="rating-h">Is It Toxic? Scientific Ratings</h3>
    <div class="rating" style="left:319px"><h4>Carcinogens</h4>“no significant risk level” (“NSRL”) means that exposure to the amount of chemical in a product would result in no more than one case of cancer out of every 100,000 individuals who were exposed to the chemical over a 70-year time period</div>
    <div class="rating" style="left:565px"><h4>Reproductive Toxins</h4>Maximum allowable dose level (“MADL”) is the level at which a chemical would have no observable effect, even if an individual were exposed to 1,000 times that level</div>
    <span class="pagenum">5</span>
  </section>

  <!-- treaty -->
  <section class="slide col-l row-2 treaty">
    <div class="bar"></div>
    <h2 class="title" style="top:30px">GEP Plastic Pollution Treaty<br><span class="light">Scientific Checks &amp; Balances</span></h2>
    <div class="panel">Some think science can provide definitive, complete and foolproof answers. But given the world’s complexity, different research modalities and replication limits, critical thinking must be embraced to develop policies that work.</div>
    <ul class="checks">
      <li><svg viewBox="0 0 16 16"><rect x="1" y="2" width="12" height="12" fill="none" stroke="#5aa04a" stroke-width="1.5"/><path d="M4 8l3 3 7-8" fill="none" stroke="#5aa04a" stroke-width="2"/></svg>The Body of Research on Plastic Is Extensive.</li>
      <li><svg viewBox="0 0 16 16"><circle cx="8" cy="8" r="6.5" fill="none" stroke="#f6a21f" stroke-width="1.5"/><path d="M6 6.5a2 2 0 1 1 2.5 2c-.5.2-.5.6-.5 1.3M8 11.6v.6" fill="none" stroke="#f6a21f" stroke-width="1.5"/></svg>Are All Plastics Toxic?</li>
      <li><svg viewBox="0 0 16 16"><circle cx="8" cy="8" r="6.5" fill="none" stroke="#f6a21f" stroke-width="1.5"/><path d="M6 6.5a2 2 0 1 1 2.5 2c-.5.2-.5.6-.5 1.3M8 11.6v.6" fill="none" stroke="#f6a21f" stroke-width="1.5"/></svg>Are NGO, GEP or Industry Interpretations Accurate or Inaccurate?</li>
      <li><svg viewBox="0 0 16 16"><rect x="2" y="2" width="12" height="12" fill="none" stroke="#6b2a14" stroke-width="1.5"/><path d="M5 5l6 6M11 5l-6 6" stroke="#6b2a14" stroke-width="2"/></svg>Is Data Transparency Evident For The Science Supporting Policy Considerations?</li>
      <li><svg viewBox="0 0 16 16"><circle cx="8" cy="8" r="6.5" fill="none" stroke="#f6a21f" stroke-width="1.5"/><path d="M6 6.5a2 2 0 1 1 2.5 2c-.5.2-.5.6-.5 1.3M8 11.6v.6" fill="none" stroke="#f6a21f" stroke-width="1.5"/></svg>Problematic Plastics Are Classified Without Criteria</li>
      <li><svg viewBox="0 0 16 16"><rect x="1" y="2" width="12" height="12" fill="none" stroke="#5aa04a" stroke-width="1.5"/><path d="M4 8l3 3 7-8" fill="none" stroke="#5aa04a" stroke-width="2"/></svg>Is Scientific Information On Plastic Pollution Being Used Out Of Context?</li>
    </ul>
    <p class="foot">Know How To Ask The Right Questions</p>
    <span class="pagenum">2</span>
  </section>

  <!-- EPS health -->
  <section class="slide col-r row-2">
    <div class="bar"></div>
    <h2 class="title" style="top:32px">Expanded Polystyrene Does Not Pose A Human<br>Health Threat</h2>
    <p class="subtitle" style="top:114px">Expanded Polystyrene Foam – Residual Styrene Emissions</p>
    <table class="eps-table">
      <tr><th>Exposure Scenario</th><th>Consumer Styrene Lifetime Average Daily Dose pg/day</th></tr>
      <tr><td>Private Office</td><td>0.05–0.79</td></tr>
      <tr><td>School Classroom</td><td>0.03–0.48</td></tr>
      <tr><td>Home Residence</td><td>0.48–7.33</td></tr>
      <tr><td>State Health Office Safe Harbor Styrene NSRL</td><td>27</td></tr>
    </table>
    <svg class="chart" viewBox="0 0 804 452" aria-label="Chart comparing EPS styrene dose to the NSRL">
      <g font-family="Poppins,sans-serif" font-size="12" fill="#2b2b2b" text-anchor="end">
        <text x="430" y="186">30</text><text x="430" y="217">25</text><text x="430" y="248">20</text><text x="430" y="279">15</text><text x="430" y="310">10</text><text x="430" y="341">5</text><text x="430" y="372">0</text>
      </g>
      <line x1="441" y1="178" x2="441" y2="368" stroke="#ccc"/>
      <polygon points="464,186 744,186 744,318 739,314 464,190" fill="#c77a0c"/>
      <polygon points="459,192 739,192 739,316 459,287" fill="#f6a21f"/>
      <polygon points="441,368 455,348 594,348 739,322 744,322 744,368" fill="#c77a0c"/>
      <polygon points="441,368 455,350 594,350 739,326 739,368" fill="#c9962a"/>
      <g font-family="Poppins,sans-serif" fill="#fff" text-anchor="middle">
        <text x="602" y="232" font-size="15">Styrene NSRL</text>
        <text x="602" y="257" font-size="15">≤27µg/day IS NOT Harmful</text>
        <text x="690" y="356" font-size="15">≤7.3µg/day</text>
      </g>
      <g font-family="Poppins,sans-serif" font-size="12" fill="#2b2b2b">
        <text x="750" y="316">NSRL</text><text x="750" y="342">EPS</text>
        <text x="453" y="391">Office</text><text x="566" y="391">School</text><text x="672" y="391">Residence</text>
      </g>
    </svg>
    <span class="pagenum">6</span>
  </section>

  <!-- NGO misuse -->
  <section class="slide col-l row-3 misuse">
    <div class="bar"></div>
    <h2 class="title" style="top:30px">NGO Misuse of Technical Data</h2>
    <p class="lead" style="top:73px">The definition of data misuse is using any information in a way it’s not supposed to be used. Terms of proper data use are usually specified in laws, industry standards, policies, and other agreements.</p>
    <div class="claim">
      <div class="org"><span class="org-mark"></span><span class="org-name">Coastal Waste Coalition</span></div>
      <p class="txt"><b>False Claim:</b> “Polystyrene foam contains styrene, which has been linked to cancer, vision and hearing loss, impaired memory and concentration, and nervous system effects.”</p>
      <p class="ref">Reference:&nbsp; Potential Toxicity of Polystyrene Micropolastics</p>
    </div>
    <div class="paper">
      <p class="jn">RESEARCH<br>LETTERS</p>
      <p class="pt">Potential toxicity of polystyrene microplastic particles</p>
      <div class="ln"></div><div class="ln"></div><div class="ln" style="width:80%"></div><div class="ln"></div><div class="ln"></div><div class="ln" style="width:60%"></div><div class="ln" style="margin-top:9px"></div><div class="ln"></div><div class="ln" style="width:70%"></div>
    </div>
    <p class="concl"><b>Research Conclusions:</b> “The study confirmed that <span class="hl">PS particles were not toxic to human cells</span> at a dosage of ~500µg/mL and PS particles with diameters of 10–11 µm were not significantly cytotoxic”. Further, “It could be concluded that PS particles are not cytotoxic to HDFs and PBMCs in usual conditions but might cause damage in extreme, high concentrations.”</p>
    <span class="pagenum">3</span>
  </section>

  <!-- break -->
  <section class="slide col-r row-3 break" role="img" aria-label="Gloved hands sifting colourful plastic pellets">
    <div class="bar white" style="top:164px"></div>
    <h2 class="centered h">Content Break Slide</h2>
    <p class="centered p">Duis aute irure dolor in reprehenderit in voluptate velit esse cillum dolore eu fugiat nulla pariatur.&nbsp; Excepteur sint occaecat cupidatat non proident, sunt in culpa qui officia deserunt mollit anim id est laborum.</p>
    <span class="pagenum">7</span>
  </section>

  <!-- atmospheric -->
  <section class="slide col-l row-4 atmo">
    <div class="bar"></div>
    <h2 class="title" style="top:36px">Atmospheric Studies In 11 Cities Have<br>Varying Results</h2>
    <p class="subtitle" style="top:114px">Does Microplastic Really Represent A Threat? A Review of Atmospheric<br>Contamination Sources &amp; Potential Impacts (2021)</p>
    <div class="panel">In 11 studies in specific locations (Europe, Asia, North America) airborne polystyrene particles were found in only three cities. The results represent three different test sample types and all three used varying air concentration calculations. Therefore, the results are incompatible</div>
    <div class="body">
      <p><u>Thematic Hypothesis:</u> Atmospheric transport of microplastics is detrimental and is of great concern to the global community.</p>
      <p style="margin-top:6px"><u>What’s Inside:</u></p>
      <ul>
        <li>There Are Three (3) Air Sampling Methodologies In This Developing Field of Study</li>
        <li>No Standard Method Exists To Prepare Airborne Microplastic Test Samples</li>
        <li>Visual Identification Methods Are Ineffective For Smaller Atmospheric Samples</li>
        <li>Studies Have Shown a Dominant Number of Airborne Microplastics are Fibers (≤95%).</li>
      </ul>
      <p><u>Bottom Line:</u> There is a need to conduct comprehensive research on sources of atmospheric microplastics to aid in the initiation of effective control mechanisms and policy measures.</p>
    </div>
    <span class="pagenum">4</span>
  </section>

  <!-- thank you -->
  <section class="slide col-r row-4 thanks" role="img" aria-label="Close-up of red and green foam texture">
    <div class="bar white" style="top:128px"></div>
    <h2 class="centered h">Thank <span>You</span></h2>
    <p class="centered p">Sed ut perspiciatis unde omnis iste natus error sit voluptatem accusanti um doloremque laudantium, totam rem aperiam, eaque ipsa quae ab illo inventore veritatis et quasi architecto beatae vitae dicta&nbsp; sunt&nbsp; explicabooccaecat cupidatat non proident.</p>
    <div class="social"><span></span><span></span><span></span></div>
    <span class="pagenum plain">8</span>
  </section>

</div>
</body>
</html>
```